BOLD & MINIMALIST DESIGN NEEDED

We want a very bold but minimalistic business card design that is impactful and utilizes both sides of the business card. Our current logo is included for your use.

We want bold fonts and good use of negative space. We don't want the logo to overpower the design.

Target Market(s)

Professionals who are building new commercial buildings.

Industry/Entity Type

Construction

Contact Information for Business Card

Name, Title, email, office phone, cell phone, website

Font styles to use
Serif
Sans Serif

Requirements
Must have
• Bold design!

```html
<!DOCTYPE html>
<html lang="en">
<head>
<meta charset="utf-8">
<title>Summitline Design + Build — Business Card</title>
<link rel="stylesheet" href="https://fonts.googleapis.com/css2?family=Montserrat:wght@400;500;600;800;900&display=swap">
<style>
  :root {
    --green: #7dc31e;
    --green-light: #c9eaa0;
    --ink: #0d0d0d;
    --card-black: #111111;
    --paper: #ffffff;
    --stage: #2c2c2c;
    --rule: #8a8a8a;
  }
  * { box-sizing: border-box; margin: 0; padding: 0; }
  html, body {
    width: 1200px; height: 866px; overflow: hidden;
    background: var(--stage);
    font-family: "Montserrat", sans-serif;
  }
  .sheet {
    width: 1200px; height: 866px;
    display: flex; align-items: center; justify-content: center; gap: 30px;
  }
  .card {
    position: relative; width: 560px; height: 320px; overflow: hidden;
    box-shadow: 0 14px 30px rgba(0,0,0,.45);
  }

  /* Front */
  .card-front { background: var(--paper); }
  .feature-art { position: absolute; inset: 0; }
  .contact-block {
    position: absolute; left: 318px; top: 92px; width: 220px;
  }
  .person-name {
    font-weight: 800; font-size: 21px; letter-spacing: .04em;
    color: var(--ink); text-transform: uppercase; line-height: 1;
  }
  .person-title {
    margin-top: 5px; font-weight: 600; font-size: 10.5px; letter-spacing: .09em;
    color: var(--green); text-transform: uppercase;
  }
  .icon-row {
    display: flex; align-items: center; gap: 5px; margin: 12px 0 11px;
  }
  .icon-row .rule { flex: 1; height: 1px; background: var(--rule); }
  .icon {
    width: 20px; height: 20px; border-radius: 3px; background: var(--green);
    display: flex; align-items: center; justify-content: center;
  }
  .icon svg { width: 12px; height: 12px; }
  .contact-line {
    font-size: 12.5px; font-weight: 500; color: var(--ink);
    line-height: 1.35; letter-spacing: .02em;
  }
  .contact-line .accent { color: var(--green); }

  /* Back */
  .card-back {
    background:
      linear-gradient(115deg, rgba(255,255,255,.035) 0 30%, transparent 30% 62%, rgba(255,255,255,.03) 62% 100%),
      var(--card-black);
    display: flex; align-items: center; justify-content: center;
  }
  .brand-lockup { text-align: center; }
  .brand-name {
    display: flex; align-items: center; gap: 10px;
    font-weight: 900; font-size: 40px; letter-spacing: .02em;
    color: var(--paper); text-transform: uppercase; line-height: 1;
  }
  .brand-mark { width: 18px; height: 18px; background: var(--green); }
  .brand-tagline {
    margin-top: 10px; font-weight: 500; font-size: 13px; letter-spacing: .42em;
    color: var(--paper); text-transform: uppercase;
    border-top: 1px solid var(--paper); padding-top: 8px;
  }
</style>
</head>
<body>
<main class="sheet">

  <section class="card card-front">
    <svg class="feature-art" viewBox="0 0 560 320" role="img" aria-label="Large green and black monogram artwork area">
      <defs>
        <linearGradient id="artFill" x1="0" y1="1" x2="1" y2="0">
          <stop offset="0" stop-color="#7dc31e"/>
          <stop offset=".6" stop-color="#a6d961"/>
          <stop offset="1" stop-color="#d8f0b8"/>
        </linearGradient>
      </defs>
      <path d="M0 0 H300 C 290 130 200 250 0 262 Z" fill="url(#artFill)"/>
      <path d="M0 262 C 200 250 290 130 300 0 H312 C 302 140 210 268 0 276 Z" fill="#0d0d0d"/>
    </svg>

    <div class="contact-block">
      <h1 class="person-name">Daniel Reeves</h1>
      <p class="person-title">Managing Director</p>
      <div class="icon-row">
        <span class="rule"></span>
        <span class="icon" title="Office phone">
          <svg viewBox="0 0 12 12"><path d="M2 1.5 L4 1.5 L5 4 L3.8 5 C4.4 6.4 5.6 7.6 7 8.2 L8 7 L10.5 8 L10.5 10 C6 10.5 1.5 6 2 1.5Z" fill="#fff"/></svg>
        </span>
        <span class="icon" title="Mobile">
          <svg viewBox="0 0 12 12"><rect x="3.2" y="1" width="5.6" height="10" rx="1" fill="none" stroke="#fff" stroke-width="1.2"/><circle cx="6" cy="9.3" r=".6" fill="#fff"/></svg>
        </span>
        <span class="icon" title="Email">
          <svg viewBox="0 0 12 12"><rect x="1" y="2.5" width="10" height="7" fill="none" stroke="#fff" stroke-width="1.1"/><path d="M1 2.5 L6 6.5 L11 2.5" fill="none" stroke="#fff" stroke-width="1.1"/></svg>
        </span>
        <span class="icon" title="Website">
          <svg viewBox="0 0 12 12"><circle cx="6" cy="6" r="4.6" fill="none" stroke="#fff" stroke-width="1.1"/><ellipse cx="6" cy="6" rx="2" ry="4.6" fill="none" stroke="#fff" stroke-width="1"/><path d="M1.4 6 H10.6" stroke="#fff" stroke-width="1"/></svg>
        </span>
        <span class="rule"></span>
      </div>
      <p class="contact-line">044-555 210 300</p>
      <p class="contact-line">044-555 210 301</p>
      <p class="contact-line">hello@summitline.com</p>
      <p class="contact-line">www.<span class="accent">summitline</span>.com</p>
    </div>
  </section>

  <section class="card card-back">
    <div class="brand-lockup">
      <div class="brand-name"><span class="brand-mark"></span>Summitline</div>
      <p class="brand-tagline">Design + Build</p>
    </div>
  </section>

</main>
</body>
</html>
```